Business Card For Halvenmoor Financial Consulting

Hi, I would like a business card designed. Bold, modern.
Please use the same design as the logo. I have also attached the website design to see the overall theme.
Wordmark Font
Color: Hex: #01AEF7

```html
<!DOCTYPE html>
<html lang="en">
<head>
<meta charset="utf-8">
<title>Halvenmoor Consulting — Business Card</title>
<link href="https://fonts.googleapis.com/css2?family=Montserrat:wght@600&family=Arimo:wght@400;700&display=swap" rel="stylesheet">
<style>
  :root {
    --brand-blue: #01aef7;
    --card-black: #181818;
    --pattern-dark: #131313;
    --pattern-light: #222222;
    --stage: #3b3b3b;
    --text-white: #f2f2f2;
  }
  * { box-sizing: border-box; margin: 0; padding: 0; }
  html, body { width: 1200px; height: 801px; overflow: hidden; }
  body {
    background: var(--stage);
    position: relative;
    font-family: "Arimo", Arial, sans-serif;
  }
  .card {
    position: absolute;
    width: 540px;
    height: 309px;
    background: var(--card-black);
    border-bottom: 3px solid var(--brand-blue);
    box-shadow: 0 12px 30px rgba(0,0,0,.45);
    top: 246px;
  }
  .card--front { left: 40px; }
  .card--back { left: 620px; overflow: hidden; }

  /* Front */
  .brand {
    position: absolute;
    left: 40px;
    top: 168px;
    display: flex;
    align-items: center;
    gap: 12px;
  }
  .brand__square {
    width: 34px; height: 34px;
    border: 3px solid var(--brand-blue);
  }
  .brand__name {
    font-family: "Montserrat", sans-serif;
    font-weight: 600;
    color: var(--text-white);
    line-height: 1.15;
  }
  .brand__main { font-size: 26px; letter-spacing: 1px; display: block; }
  .brand__sub { font-size: 10px; letter-spacing: 8px; display: block; }

  .divider {
    position: absolute;
    left: 300px;
    top: 40px;
    width: 1px;
    height: 190px;
    background: var(--brand-blue);
  }
  .contact {
    position: absolute;
    left: 318px;
    top: 46px;
    color: var(--text-white);
    font-size: 12.5px;
    line-height: 1.35;
  }
  .contact__name {
    color: var(--brand-blue);
    font-weight: 700;
    font-size: 19px;
    letter-spacing: -.3px;
  }
  .contact__title { margin-bottom: 12px; font-size: 13px; }
  .contact__address { margin-bottom: 12px; }
  .contact__line { display: flex; align-items: center; gap: 6px; }
  .contact__line svg { width: 11px; height: 11px; flex: none; }

  /* Back */
  .back__pattern {
    position: absolute; inset: 0;
    background: linear-gradient(135deg, var(--pattern-light), var(--pattern-dark) 60%, var(--pattern-light));
  }
  .back__brand {
    position: absolute;
    right: 60px;
    top: 150px;
    font-family: "Montserrat", sans-serif;
    font-weight: 600;
    font-size: 20px;
    letter-spacing: 1px;
    color: var(--brand-blue);
  }
</style>
</head>
<body>
  <section class="card card--front">
    <div class="brand">
      <div class="brand__square"></div>
      <div class="brand__name">
        <span class="brand__main">HALVENMOOR</span>
        <span class="brand__sub">CONSULTING</span>
      </div>
    </div>
    <div class="divider"></div>
    <div class="contact">
      <p class="contact__name">MARLO TEVERIN</p>
      <p class="contact__title">President</p>
      <p class="contact__address">1480 Seabrook Harbor<br>Coral Bay CA 90417</p>
      <p class="contact__line">
        <svg viewBox="0 0 12 12"><path fill="#01aef7" d="M2.5 1l2 2.2-1 1.3a7 7 0 0 0 4 4l1.3-1L11 9.5 9.6 11C5 11 1 7 1 2.4z"/></svg>
        555-014-2290
      </p>
      <p class="contact__line">
        <svg viewBox="0 0 12 12"><rect x="1" y="2.5" width="10" height="7" fill="#01aef7"/><path d="M1 2.5l5 4 5-4" stroke="#181818" fill="none"/></svg>
        info@HalvenmoorConsulting.com
      </p>
      <p class="contact__line">
        <svg viewBox="0 0 12 12"><circle cx="6" cy="6" r="5" fill="#01aef7"/><path d="M1 6h10M6 1c-2.5 3-2.5 7 0 10M6 1c2.5 3 2.5 7 0 10" stroke="#181818" fill="none" stroke-width=".8"/></svg>
        www.HalvenmoorConsulting.com
      </p>
    </div>
  </section>

  <section class="card card--back">
    <div class="back__pattern" role="img" aria-label="Repeating embossed tile pattern in dark tones"></div>
    <p class="back__brand">HALVENMOOR</p>
  </section>
</body>
</html>
```